Zenqo - revolutionary mobile payment

The app is a P2P money trasfert, without the using of credit card or bank circuits it can transfer electronic money from one person to another consumers simply and immediatelly.
You can use the color you want, but the message we need to transert to consumer is simplicity, safety and coolness.
In attach the logo of the company and the wireframe of thre page of the app.
The goal is to design the page of the app with a clear, simple and intuitive graphic.
Updates

I have upgrade the brief with important information and detail, many thanks

Target Market(s)

all the people

Industry/Entity Type

Credit Card

Requirements
Must have
• You have to design one icon for each button in the first page, (shop is: where to shop)
in the second one a new intuitive image (instead of the hand) that let the user to understand that with a simple swipe he can process the payment
Nice to have
• You can include or esxclude what you want or belive can improve user experience of the app
Should not have
• too much color, too much button or information

```html
<!DOCTYPE html>
<html lang="en">
<head>
<meta charset="utf-8">
<title>Zenqo – Home</title>
<link rel="stylesheet" href="https://fonts.googleapis.com/css2?family=Source+Sans+3:wght@400;500&display=swap">
<style>
  :root {
    --navy: #1b2f63;
    --band: #cfdeec;
    --tile: #ffffff;
    --tile-edge: #e4e6ea;
    --grid-bg: #f3f4f6;
    --stage: #e9ebee;
    --white: #ffffff;
    --ink: #2d3440;
    --avatar-a: #c89a7e;
    --avatar-b: #6b4a3a;
  }
  * { box-sizing: border-box; margin: 0; padding: 0; }
  html, body {
    width: 1200px; height: 750px; overflow: hidden;
    background: var(--stage);
    font-family: "Source Sans 3", "Helvetica Neue", Arial, sans-serif;
  }
  .stage { position: relative; width: 1200px; height: 750px; }
  .screen {
    position: absolute; left: 389px; top: 0;
    width: 450px; height: 800px;
    transform: scale(0.9375); transform-origin: top left;
    background: var(--grid-bg);
    box-shadow: 0 0 24px rgba(0,0,0,.12);
  }
  .app-header { height: 92px; background: var(--navy); color: var(--white); position: relative; }
  .status-bar {
    height: 28px; display: flex; align-items: center; justify-content: space-between;
    padding: 0 8px; font-size: 15px;
  }
  .status-left, .status-right { display: flex; align-items: center; gap: 6px; width: 140px; }
  .status-right { justify-content: flex-end; }
  .signal { display: flex; gap: 2px; }
  .signal span { width: 8px; height: 8px; border-radius: 50%; border: 1px solid var(--white); }
  .signal span.on { background: var(--white); }
  .status-time { font-weight: 500; }
  .phone-number { position: absolute; left: 25px; top: 48px; font-size: 19px; letter-spacing: .3px; }
  .settings { position: absolute; right: 12px; top: 40px; width: 36px; height: 36px; }
  .profile-band {
    height: 78px; background: var(--band);
    display: flex; align-items: center; padding-left: 18px; gap: 15px;
  }
  .avatar {
    width: 56px; height: 56px; border-radius: 50%;
    background: radial-gradient(circle at 50% 45%, var(--avatar-a), var(--avatar-b));
    border: 2px solid var(--white);
  }
  .plan { font-size: 19px; color: var(--ink); }
  .action-grid {
    position: absolute; left: 13px; top: 185px;
    display: grid; grid-template-columns: 210px 210px; grid-template-rows: 295px 294px;
    gap: 8px;
  }
  .action-tile {
    background: var(--tile); border: 1px solid var(--tile-edge);
    color: var(--navy);
    display: flex; flex-direction: column; align-items: center; justify-content: center;
    gap: 22px; font-size: 41px; text-decoration: none;
  }
  .action-tile.is-active { background: var(--navy); color: var(--white); border-color: var(--navy); }
  .action-tile svg { width: 92px; height: 66px; fill: none; stroke: currentColor; stroke-width: 3.4; stroke-linejoin: round; stroke-linecap: round; }
</style>
</head>
<body>
<main class="stage">
  <section class="screen" aria-label="Zenqo home screen">
    <header class="app-header">
      <div class="status-bar">
        <div class="status-left">
          <div class="signal"><span class="on"></span><span class="on"></span><span class="on"></span><span></span><span></span></div>
          <svg width="18" height="14" viewBox="0 0 18 14" fill="none" stroke="#fff" stroke-width="1.8" stroke-linecap="round"><path d="M1 5a11 11 0 0 1 16 0"/><path d="M4 8a7 7 0 0 1 10 0"/><circle cx="9" cy="12" r="1.3" fill="#fff" stroke="none"/></svg>
        </div>
        <div class="status-time">4:39 PM</div>
        <div class="status-right">
          <span>100%</span>
          <svg width="34" height="15" viewBox="0 0 34 15"><rect x="1" y="1" width="29" height="13" rx="2.5" fill="none" stroke="#fff" stroke-width="1.4"/><rect x="3" y="3" width="25" height="9" rx="1" fill="#fff"/><rect x="31" y="5" width="2" height="5" fill="#fff"/></svg>
        </div>
      </div>
      <div class="phone-number">+325550148207</div>
      <svg class="settings" viewBox="0 0 36 36" fill="none" stroke="#fff" stroke-width="1.8" aria-label="Settings">
        <path d="M16 3h4l1 4 3 1.3 3.5-2.2 2.8 2.8-2.2 3.5L29.4 15l4 1v4l-4 1-1.3 3 2.2 3.5-2.8 2.8-3.5-2.2-3 1.3-1 4h-4l-1-4-3-1.3-3.5 2.2-2.8-2.8 2.2-3.5L6.6 21l-4-1v-4l4-1 1.3-3-2.2-3.5 2.8-2.8 3.5 2.2L15 7z"/>
        <circle cx="18" cy="18" r="5"/>
      </svg>
    </header>

    <div class="profile-band">
      <div class="avatar" role="img" aria-label="User profile photo"></div>
      <span class="plan">Basic</span>
    </div>

    <nav class="action-grid">
      <a class="action-tile is-active" href="#pay">
        <svg viewBox="0 0 92 66"><rect x="14" y="4" width="74" height="44"/><rect x="8" y="10" width="74" height="44"/><rect x="2" y="16" width="74" height="46" fill="var(--navy)"/><text x="39" y="50" text-anchor="middle" font-size="32" font-family="Source Sans 3, sans-serif" font-weight="500" fill="currentColor" stroke="none">$</text></svg>
        <span>Pay</span>
      </a>
      <a class="action-tile" href="#ask">
        <svg viewBox="0 0 92 66"><path d="M54 22H12v36h66V36"/><line x1="22" y1="34" x2="46" y2="34"/><line x1="22" y1="44" x2="40" y2="44"/><path d="M62 40l3-10 18-26 6 4-18 26z"/><path d="M62 40l-4 8"/><path d="M48 48h14"/></svg>
        <span>Ask</span>
      </a>
      <a class="action-tile" href="#account">
        <svg viewBox="0 0 92 66"><rect x="8" y="4" width="74" height="56" rx="2"/><line x1="8" y1="16" x2="82" y2="16"/><circle cx="15" cy="10" r="1" fill="currentColor"/><circle cx="21" cy="10" r="1" fill="currentColor"/><circle cx="27" cy="10" r="1" fill="currentColor"/><rect x="36" y="34" width="18" height="16" rx="1.5"/><path d="M39 34v-5a6 6 0 0 1 12 0v5"/></svg>
        <span>Account</span>
      </a>
      <a class="action-tile" href="#shop">
        <svg viewBox="0 0 92 66"><path d="M4 10h10l8 32h40l6-22H30"/><line x1="26" y1="29" x2="66" y2="29"/><line x1="40" y1="20" x2="42" y2="42"/><line x1="54" y1="20" x2="52" y2="42"/><path d="M22 42l-3 8h45"/><circle cx="28" cy="57" r="4"/><circle cx="58" cy="57" r="4"/><circle cx="74" cy="13" r="10"/><line x1="74" y1="7" x2="74" y2="19"/><line x1="68" y1="13" x2="80" y2="13"/></svg>
        <span>Shop</span>
      </a>
    </nav>
  </section>
</main>
</body>
</html>
```